BrightLedgerMoney(.com) needs website & logo design

We need our website mock-up made into a reality! We are wanting to launch a multifaceted website for all things financial - i.e. blogs, financial wellness information, and a network of redirect links.
We have an existing mock-up, which I will include, but are open to your creative approach!

Industry/Entity Type

Finance

Coding

Coded - Design and coding required

Number of Pages Required

1 page

Requirements
Must have
• Corresponding logo

```html
<!DOCTYPE html>
<html lang="en">
<head>
<meta charset="utf-8">
<title>Bright Ledger Money</title>
<link href="https://fonts.googleapis.com/css2?family=Audiowide&family=Raleway:wght@400;500;600&family=Roboto:wght@400;500;700&display=swap" rel="stylesheet">
<style>
:root{
  --teal:#72dcc2;
  --teal-dark:#2f6f60;
  --purple:#a08ac7;
  --purple-line:#9b86c8;
  --ink:#111111;
  --text:#3a3a3a;
  --muted:#9a9a9a;
  --band:#f4f4f4;
  --card:#f6f6f6;
  --white:#ffffff;
}
*{margin:0;padding:0;box-sizing:border-box}
html,body{width:1200px;height:3723px;overflow:hidden;background:var(--white)}
body{position:relative;font-family:'Raleway',sans-serif;color:var(--text)}
.abs{position:absolute}
.display{font-family:'Audiowide',sans-serif;color:var(--ink);font-weight:400}
.btn{position:absolute;display:flex;align-items:center;justify-content:center;background:var(--teal);color:var(--teal-dark);border-radius:24px;font-family:'Raleway',sans-serif;font-size:15px}

/* hero */
.hero{position:absolute;left:0;top:0;width:1200px;height:620px;overflow:hidden}
.hero-photo{position:absolute;inset:0;background:
  radial-gradient(ellipse at 30% 25%,#fff6e6 0%,rgba(255,246,230,0) 55%),
  radial-gradient(ellipse at 85% 60%,#c79a68 0%,rgba(199,154,104,0) 45%),
  linear-gradient(180deg,#e9d9c4 0%,#f2e2cb 40%,#e4c8a6 75%,#c9a98a 100%)}
.hero-wave{position:absolute;left:0;bottom:0}
.menu-icon{position:absolute;left:62px;top:46px}
.brand{position:absolute;left:126px;top:42px;font-family:'Audiowide',sans-serif;font-size:19px;color:var(--ink)}
.hero-title{position:absolute;left:111px;top:196px;font-size:40px;line-height:42px}
.hero-sub{position:absolute;left:113px;top:302px;width:420px;font-size:17px;line-height:29px;color:#333}

.signup{position:absolute;left:111px;top:509px;width:978px;height:150px;background:var(--white);border-radius:12px;box-shadow:0 4px 18px rgba(0,0,0,.12)}
.signup-label{position:absolute;left:67px;top:58px;font-family:'Audiowide',sans-serif;font-size:23px;color:var(--ink)}
.signup-input{position:absolute;left:282px;top:46px;width:446px;height:54px;border:1px solid #cfcfcf;border-radius:12px}

/* tools */
.tool{position:absolute;top:755px;width:180px;margin-left:-90px;text-align:center}
.tool svg{display:block;margin:0 auto;height:70px}
.tool span{display:block;margin-top:36px;font-family:'Roboto',sans-serif;font-weight:500;font-size:19px;color:var(--ink)}

/* feature */
.feature{position:absolute;left:0;top:954px;width:1200px;height:350px;background:var(--band)}
.feature-photo{position:absolute;left:0;top:52px;width:531px;height:250px;border-radius:0 18px 18px 0;border-right:6px solid var(--purple);background:linear-gradient(100deg,#6a6a6a 0%,#b8a58b 35%,#d9cdbd 60%,#8f8478 100%)}
.feature-title{position:absolute;left:600px;top:72px;font-size:31px;line-height:36px}
.feature-text{position:absolute;left:600px;top:166px;width:486px;font-size:16.5px;line-height:29px;text-align:justify}

/* topics */
.topic{position:absolute;width:282px;height:224px;background:var(--card);border-radius:12px;text-align:center}
.topic svg{position:absolute;left:50%;top:44px;transform:translateX(-50%)}
.topic span{position:absolute;left:0;right:0;top:160px;font-family:'Roboto',sans-serif;font-weight:500;font-size:23px;color:var(--ink)}

/* blog */
.blog{position:absolute;left:0;top:1992px;width:1200px;height:770px;background:var(--band)}
.blog-title{position:absolute;left:0;right:0;top:60px;text-align:center;font-size:32px}
.arrow{position:absolute;top:49px;width:58px;height:58px;border-radius:50%;background:var(--teal);display:flex;align-items:center;justify-content:center}
.post{position:absolute;top:143px}
.post-img{height:214px;border-radius:4px}
.post h3{font-family:'Audiowide',sans-serif;font-weight:400;font-size:22px;color:var(--ink);margin:36px 0 0 5px}
.post p{margin:8px 0 0 5px;width:292px;font-size:16.5px;line-height:29px;text-align:justify}
.post time{display:block;margin:10px 0 0 5px;font-size:10px;color:var(--muted)}

.wellness-title{position:absolute;left:0;right:0;top:2835px;text-align:center;font-size:34px}
.wellness-text{position:absolute;left:100px;right:100px;top:2893px;text-align:center;font-size:16.5px;line-height:29px}

/* questions */
.questions{position:absolute;left:0;top:3032px;width:1200px;height:279px;background:var(--purple)}
.questions h2{position:absolute;left:111px;top:70px;font-family:'Audiowide',sans-serif;font-weight:400;font-style:italic;font-size:29px;color:var(--white)}
.questions p{position:absolute;left:111px;top:127px;width:680px;font-size:16.5px;line-height:29px;color:var(--white)}

/* footer */
.footer-brand{position:absolute;left:113px;top:3381px;font-family:'Audiowide',sans-serif;font-size:29px;line-height:42px;color:var(--ink)}
.social{position:absolute;left:113px;top:3496px;display:flex;gap:18px}
.social i{width:18px;height:18px;border-radius:50%;background:var(--purple)}
.fcol{position:absolute;top:3383px;font-size:16px;color:#333}
.fcol h4{font-family:'Roboto',sans-serif;font-weight:700;font-size:16.5px;color:var(--ink);margin-bottom:18px}
.fcol li{list-style:none;line-height:41px}
.fcol.latest li{line-height:19px;margin-bottom:22px}
.footer-rule{position:absolute;left:111px;top:3655px;width:978px;height:1px;background:#e2e2e2}
.copyright{position:absolute;left:0;right:0;top:3678px;text-align:center;font-size:14px;color:#333}
</style>
</head>
<body>

<header class="hero">
  <div class="hero-photo" role="img" aria-label="People jumping at sunset beside growing stacks of coins with seedlings"></div>
  <svg class="hero-wave" width="1200" height="80" viewBox="0 0 1200 80">
    <path d="M0 40 Q60 60 120 66 L120 80 L0 80Z" fill="var(--purple)"/>
    <path d="M1080 60 Q1150 40 1200 50 L1200 80 L1080 80Z" fill="var(--purple)"/>
  </svg>
  <svg class="menu-icon" width="22" height="18" viewBox="0 0 22 18"><rect y="0" width="22" height="3.5" fill="#111"/><rect y="7" width="22" height="3.5" fill="#111"/><rect y="14" width="22" height="3.5" fill="#111"/></svg>
  <div class="brand">Bright Ledger Money</div>
  <div class="btn" style="left:953px;top:33px;width:133px;height:45px">Contact</div>
  <h1 class="display hero-title">A Bright Ledger To<br>Financial Wellness</h1>
  <p class="hero-sub">Having insight to relevant information is what we bring to you in a clear and easy to digest way</p>
  <div class="btn" style="left:111px;top:393px;width:132px;height:45px">GetStarted</div>
</header>

<section class="signup">
  <div class="signup-label">Signup For Free</div>
  <div class="signup-input"></div>
  <div class="btn" style="left:775px;top:51px;width:133px;height:45px">Submit</div>
</section>

<section class="tools">
  <div class="tool" style="left:147px"><svg viewBox="0 0 60 60" width="60"><circle cx="26" cy="28" r="16" fill="none" stroke="#111" stroke-width="2.5"/><line x1="38" y1="40" x2="50" y2="52" stroke="#111" stroke-width="2.5"/></svg><span>SEARCH</span></div>
  <div class="tool" style="left:320px"><svg viewBox="0 0 60 60" width="60"><path d="M20 30a12 12 0 1 1 20 0c-3 4-4 6-4 10h-12c0-4-1-6-4-10z" fill="none" stroke="#111" stroke-width="2"/><line x1="24" y1="46" x2="36" y2="46" stroke="#111" stroke-width="2"/><line x1="26" y1="51" x2="34" y2="51" stroke="#111" stroke-width="2"/><path d="M30 2v6M12 9l4 4M48 9l-4 4M6 24h5M49 24h5" stroke="#111" stroke-width="2"/></svg><span>BUDGET</span></div>
  <div class="tool" style="left:507px"><svg viewBox="0 0 60 60" width="60"><rect x="6" y="6" width="48" height="50" rx="3" fill="none" stroke="#111" stroke-width="2"/><line x1="30" y1="6" x2="30" y2="56" stroke="#111" stroke-width="2"/><line x1="6" y1="31" x2="54" y2="31" stroke="#111" stroke-width="2"/><path d="M18 13v10M13 18h10M36 18h10M13 39l9 9M22 39l-9 9M36 41h10M36 46h10" stroke="#111" stroke-width="2"/></svg><span>CALCULATE</span></div>
  <div class="tool" style="left:690px"><svg viewBox="0 0 64 60" width="64"><rect x="4" y="8" width="56" height="36" rx="2" fill="none" stroke="#111" stroke-width="2"/><path d="M26 44l-4 10h20l-4-10M16 54h32" stroke="#111" stroke-width="2" fill="none"/><circle cx="40" cy="10" r="7" fill="#fff" stroke="#111" stroke-width="2"/><path d="M14 38V26M22 38V20M44 38V28M50 38V22" stroke="#111" stroke-width="3"/></svg><span>TRACK</span></div>
  <div class="tool" style="left:873px"><svg viewBox="0 0 64 64" width="64"><rect x="6" y="4" width="36" height="46" fill="none" stroke="#111" stroke-width="2"/><path d="M12 14h24M12 20h24M12 26h16M12 32h14" stroke="#111" stroke-width="2"/><circle cx="40" cy="40" r="9" fill="#fff" stroke="#111" stroke-width="2"/><line x1="47" y1="47" x2="58" y2="58" stroke="#111" stroke-width="3"/></svg><span>REASEARCH</span></div>
  <div class="tool" style="left:1057px"><svg viewBox="0 0 60 60" width="60"><path d="M8 52V42M16 52V36M24 52V30M32 52V24" stroke="#111" stroke-width="4"/><path d="M8 32L40 10M32 10h8v8" stroke="#111" stroke-width="2" fill="none"/><circle cx="44" cy="44" r="10" fill="none" stroke="#111" stroke-width="2"/><path d="M44 38v12M41 41h5a2 2 0 0 1 0 4h-4a2 2 0 0 0 0 4h5" stroke="#111" stroke-width="1.5" fill="none"/></svg><span>INVEST</span></div>
</section>

<section class="feature">
  <div class="feature-photo" role="img" aria-label="Smiling father and daughter holding a pink piggy bank at home"></div>
  <h2 class="display feature-title">TRENDING IN 2021:<br>FINANCIAL LITERACY</h2>
  <p class="feature-text">Lorem ipsum dolor sit amet, consectetur adipiscing elit, sed do eiusmod tempor incididunt ut labore et dolore magna aliqua. Quis ipsum suspendisse ultrices gravida. Risus commodo viverra maecenas accumsan lacus vel facilisis.</p>
</section>

<section class="topics">
  <div class="topic" style="left:111px;top:1430px"><svg width="84" height="84" viewBox="0 0 84 84" fill="none" stroke="var(--purple-line)" stroke-width="2.5"><rect x="6" y="6" width="46" height="72" rx="2"/><rect x="20" y="2" width="18" height="8"/><path d="M14 22h6v6h-6zM14 38h6v6h-6zM14 54h6v6h-6zM26 25h18M26 41h18M26 57h14"/><circle cx="62" cy="60" r="14"/><circle cx="62" cy="60" r="7"/><path d="M62 60l16-16M72 42l6 2"/></svg><span>Set Goals</span></div>
  <div class="topic" style="left:460px;top:1430px"><svg width="84" height="84" viewBox="0 0 84 84" fill="none" stroke="var(--purple-line)" stroke-width="2.5"><circle cx="48" cy="18" r="14"/><path d="M48 10v16M44 14h6a2 2 0 0 1 0 4h-4a2 2 0 0 0 0 4h6"/><path d="M4 62l12-12h16l12 4h8a4 4 0 0 1 0 8H36M44 62l24-12a5 5 0 0 1 6 8L48 74H22l-8 6"/></svg><span>Money 101</span></div>
  <div class="topic" style="left:808px;top:1430px"><svg width="84" height="84" viewBox="0 0 84 84" fill="none" stroke="var(--purple-line)" stroke-width="3"><path d="M42 8a34 34 0 1 0 34 34H42z"/><path d="M48 4a32 32 0 0 1 32 32H48z"/><circle cx="40" cy="44" r="18"/><path d="M40 32v24M35 37h8a3 3 0 0 1 0 6h-6a3 3 0 0 0 0 6h8"/></svg><span>Budgeting</span></div>
  <div class="topic" style="left:111px;top:1692px"><svg width="84" height="84" viewBox="0 0 84 84" fill="none" stroke="var(--purple-line)" stroke-width="2.5"><path d="M42 8v68M54 20c-4-4-8-5-14-5-9 0-14 5-14 11 0 14 30 8 30 24 0 7-6 12-15 12-7 0-12-2-16-6"/><path d="M48 22c-3-2-5-3-8-3M30 50c3 3 6 5 11 5"/></svg><span>Credit Mindfulness</span></div>
  <div class="topic" style="left:460px;top:1692px"><svg width="92" height="90" viewBox="0 0 92 90" fill="none" stroke="var(--purple-line)" stroke-width="2.5"><path d="M38 8a32 32 0 1 0 32 32H38z"/><path d="M44 4a30 30 0 0 1 30 30H44z"/><rect x="36" y="54" width="50" height="28" rx="3" fill="#f6f6f6"/><text x="61" y="75" font-family="Roboto, sans-serif" font-size="17" font-weight="500" fill="var(--purple-line)" stroke="none" text-anchor="middle">DEBT</text><path d="M60 30h16M60 38h16M60 46h16"/></svg><span>Debt Management</span></div>
  <div class="topic" style="left:808px;top:1692px"><svg width="92" height="88" viewBox="0 0 92 88" fill="none" stroke="var(--purple-line)" stroke-width="2.5"><rect x="4" y="10" width="76" height="62" rx="3"/><path d="M4 24h76M18 4v12M34 4v12M50 4v12M66 4v12"/><path d="M12 32h10v8H12zM28 32h10v8H28zM44 32h10v8H44zM60 32h10v8H60zM12 46h10v8H12zM28 46h10v8H28zM44 46h10v8H44zM12 60h10v8H12z"/><circle cx="70" cy="66" r="14" fill="#f6f6f6"/><path d="M66 58v16M66 58h6a3 3 0 0 1 0 8h-6M66 66h7a4 4 0 0 1 0 8h-7"/></svg><span>Retirement Planning</span></div>
</section>

<section class="blog">
  <h2 class="display blog-title">BLOG</h2>
  <div class="arrow" style="left:950px"><svg width="16" height="16" viewBox="0 0 16 16"><path d="M10 3L5 8l5 5" stroke="#fff" stroke-width="2.2" fill="none"/></svg></div>
  <div class="arrow" style="left:1030px"><svg width="16" height="16" viewBox="0 0 16 16"><path d="M6 3l5 5-5 5" stroke="#fff" stroke-width="2.2" fill="none"/></svg></div>

  <article class="post" style="left:114px"><div class="post-img" style="width:315px;background:linear-gradient(135deg,#5b5550,#8b7a68 50%,#3d4a5e)" role="img" aria-label="Hands holding a chalkboard reading financial literacy"></div><h3>LOREM IPSUM</h3><p>Lorem ipsum dolor sit amet, consectetur adipiscing elit, sed do eiusmod tempor incididunt ut labore et dolore magna aliqua.</p><time>20-03-2023 &nbsp;|&nbsp; Monday</time></article>
  <article class="post" style="left:442px"><div class="post-img" style="width:316px;background:linear-gradient(135deg,#3b3a3c,#8a8f96 45%,#c9ccd2 70%,#7a6c66)" role="img" aria-label="Desk with laptop, phone and printed financial charts"></div><h3>LOREM IPSUM</h3><p>Lorem ipsum dolor sit amet, consectetur adipiscing elit, sed do eiusmod tempor incididunt ut labore et dolore magna aliqua.</p><time>20-03-2023 &nbsp;|&nbsp; Monday</time></article>
  <article class="post" style="left:788px"><div class="post-img" style="width:302px;background:linear-gradient(135deg,#2c3a55,#6f7a8f 45%,#d8d6d2 75%,#9fb2c8)" role="img" aria-label="Business people reviewing charts on a tablet"></div><h3>LOREM IPSUM</h3><p>Lorem ipsum dolor sit amet, consectetur adipiscing elit, sed do eiusmod tempor incididunt ut labore et dolore magna aliqua.</p><time>20-03-2023 &nbsp;|&nbsp; Monday</time></article>

  <div class="btn" style="left:533px;top:623px;width:133px;height:45px">View More</div>
</section>
<svg class="abs" style="left:0;top:2690px" width="1200" height="80" viewBox="0 0 1200 80"><path d="M0 0 Q150 72 420 64 Q760 52 1200 20 L1200 80 L0 80Z" fill="#fff"/></svg>

<section class="wellness">
  <h2 class="display wellness-title">FINANCIAL WELLNESS 101</h2>
  <p class="wellness-text">Lorem ipsum dolor sit amet, consectetur adipiscing elit, sed do eiusmod tempor incididunt ut labore et dolore magna aliqua.<br>Quis ipsum suspendisse ultrices gravida. Risus commodo viverra maecenas accumsan lacus vel facilisis.</p>
</section>

<section class="questions">
  <h2>Have Any Questions?</h2>
  <p>Lorem ipsum dolor sit amet, consectetur adipiscing elit, sed do eiusmod tempor incididunt ut labore et dolore magna aliqua. Quis ipsum suspendisse ultrices gravida. Risus commodo viverra maecenas accumsan lacus vel facilisis.</p>
  <div class="btn" style="left:954px;top:126px;width:132px;height:45px">Contact Us</div>
</section>

<footer>
  <div class="footer-brand">Bright Ledger<br>Money</div>
  <div class="social"><i></i><i></i><i></i><i></i><i></i></div>
  <div class="fcol latest" style="left:348px"><h4>Latest Post</h4><ul><li>Hello World!</li><li>Successful Marketing<br>Ads for Your</li></ul></div>
  <div class="fcol" style="left:573px"><h4>Quick Links</h4><ul><li>Home</li><li>About Us</li><li>Services</li><li>Blog</li><li>Contact Us</li></ul></div>
  <div class="fcol" style="left:727px"><h4>Help Links</h4><ul><li>Support</li><li>FAQ</li><li>Terms &amp; Condition</li><li>Privacy Policy</li></ul></div>
  <div class="fcol" style="left:928px"><h4>Contact</h4><ul><li>+1 555 014 2277</li><li>info@brightledgermoney.com</li></ul></div>
  <div class="footer-rule"></div>
  <p class="copyright">© Copyrights 2023 Bright Ledger Money | All Rights Reserved</p>
</footer>

</body>
</html>
```